Kelvara Pane Works Business Card

We need a business card design that is suitable for a Glazing Business. We Specialize in Repairing broken windows and doors and are a 24hr on call service. We manufacture Shower screens, Fly screens, Wardrobe doors, Security doors and grilles + mirrors. We stock a variety of mesh including Standard mesh, Pet resistant mesh, Tressmet & Clearweft. We would like to use a combination of Light Blue, Dark Blue, Black & White with perhaps a picture of glass breaking.

Industry/Entity Type

Business

Contact Information for Business Card

Narooma Glass Service60B Glasshouse Rocks RdNarooma NSW 2546PH / FAX - 02 44765210MOB - 0419682350 Andrewemail - kelvarapane@fenmail.example

Font styles to use
Serif

Colors
34a7d8
0255a3
ffffff

Requirements
Must have
• logo with picture of broken or cracked glass

```html
<!DOCTYPE html>
<html lang="en">
<head>
<meta charset="utf-8">
<title>Kelvara Pane Works – Business Card</title>
<link href="https://fonts.googleapis.com/css2?family=Lato:wght@400;700&display=swap" rel="stylesheet">
<style>
  :root {
    --brand-blue: #075ee8;
    --ink: #1a1a1a;
    --paper: #ffffff;
    --backdrop: #ecebe9;
    --mark: #0a3f9c;
  }
  * { margin: 0; padding: 0; box-sizing: border-box; }
  html, body { width: 1200px; height: 900px; overflow: hidden; }
  body {
    position: relative;
    background: var(--backdrop);
    font-family: "Lato", Arial, sans-serif;
  }
  .card {
    position: absolute;
    border-radius: 18px;
    overflow: hidden;
    box-shadow: 0 6px 18px rgba(0,0,0,0.15);
  }
  .card--front { left: 78px; top: 35px; width: 588px; height: 363px; background: var(--paper); }
  .card--back { left: 390px; top: 507px; width: 565px; height: 348px; background: var(--brand-blue); }

  .band { position: absolute; left: 0; right: 0; }
  .card--front .band { top: 28px; height: 99px; background: var(--brand-blue); }
  .card--back .band { top: 40px; height: 95px; background: var(--paper); }

  .band-gap { position: absolute; top: 0; height: 100%; }
  .card--front .band-gap { left: 216px; width: 137px; background: var(--paper); }
  .card--back .band-gap { left: 224px; width: 121px; background: var(--brand-blue); }

  .brand-square { position: absolute; width: 70px; height: 70px; }
  .card--front .brand-square { left: 250px; top: 42px; background: var(--mark); }
  .card--back .brand-square { left: 250px; top: 52px; background: var(--paper); }

  .wordmark {
    position: absolute; left: 0; right: 0; text-align: center;
    font-weight: 400; line-height: 1;
  }
  .wordmark__main { display: block; font-size: 44px; letter-spacing: 0.5px; }
  .wordmark__sub { display: block; font-size: 23px; letter-spacing: 4px; margin-top: 6px; }
  .card--front .wordmark { top: 137px; left: 0; width: 588px; padding-right: 28px; color: var(--brand-blue); }
  .card--back .wordmark { top: 150px; color: var(--paper); }

  .contact-list {
    position: absolute; right: 320px; top: 245px;
    list-style: none; text-align: right;
    font-size: 16px; color: var(--ink);
  }
  .contact-list li { height: 24.5px; line-height: 24px; display: flex; justify-content: flex-end; align-items: center; gap: 6px; }
  .contact-list svg { width: 12px; height: 12px; fill: var(--brand-blue); }

  .person { position: absolute; left: 327px; top: 246px; }
  .person__name { font-size: 21px; font-weight: 700; color: var(--brand-blue); }
  .person__address { margin-top: 16px; font-size: 16px; line-height: 24px; color: var(--ink); }

  .services {
    position: absolute; top: 236px; list-style: none;
    color: var(--paper); font-size: 15.5px; font-weight: 700;
  }
  .services li { height: 25.5px; line-height: 25px; }
  .services--left { right: 299px; top: 246px; text-align: right; }
  .services--left li::after { content: ""; display: inline-block; width: 8px; height: 8px; border-radius: 50%; background: var(--paper); margin-left: 9px; vertical-align: 2px; }
  .services--right { left: 292px; top: 234px; }
  .services--right li::before { content: ""; display: inline-block; width: 8px; height: 8px; border-radius: 50%; background: var(--paper); margin-right: 9px; vertical-align: 2px; }
</style>
</head>
<body>
  <section class="card card--front" aria-label="Business card front">
    <div class="band"><div class="band-gap"></div></div>
    <div class="brand-square"></div>
    <h1 class="wordmark"><span class="wordmark__main">KELVARA</span><span class="wordmark__sub">PANE WORKS</span></h1>

    <ul class="contact-list">
      <li>02 48931067 <svg viewBox="0 0 12 12"><path d="M2.5 1l2 2-1 1.5c.7 1.5 1.8 2.6 3.2 3.2L8.2 6.7l2 2-1 2C5 10.5 1.5 7 1.3 2.2z"/></svg></li>
      <li>02 48931067 <svg viewBox="0 0 12 12"><rect x="1" y="4" width="10" height="7" rx="1"/><rect x="3" y="1" width="6" height="3" fill="#fff" stroke="#075ee8"/></svg></li>
      <li>0419682350 <svg viewBox="0 0 12 12"><path d="M3 0h6a1 1 0 011 1v10a1 1 0 01-1 1H3a1 1 0 01-1-1V1a1 1 0 011-1zm0.6 1.5v8h4.8v-8z"/></svg></li>
      <li>kelvarapane@fenmail.example <svg viewBox="0 0 12 12"><path d="M1 2.5h10v7H1z"/><path d="M1 2.5l5 4 5-4" fill="none" stroke="#fff"/></svg></li>
    </ul>

    <div class="person">
      <p class="person__name">Malcolm</p>
      <p class="person__address">17C Tindale Ridge Rd<br>Kelvara NSW 2590</p>
    </div>
  </section>

  <section class="card card--back" aria-label="Business card back">
    <div class="band"><div class="band-gap"></div></div>
    <div class="brand-square"></div>
    <h2 class="wordmark"><span class="wordmark__main">KELVARA</span><span class="wordmark__sub">PANE WORKS</span></h2>

    <ul class="services services--left">
      <li>Security doors</li>
      <li>Grilles + mirrors</li>
    </ul>
    <ul class="services services--right">
      <li>Shower screens</li>
      <li>Fly screens</li>
      <li>Wardrobe doors</li>
    </ul>
  </section>
</body>
</html>
```